Business Card Design needed for start up company Halvora

In need of a new business card designed for a start up company based in Sydney, Halvora is a new start up innovative Company, our mission it to make property accessible for everyday Australian and to become the leading Real Estate platform in Australia. We want it to be fresh and clean.

Industry/Entity Type

Financial

Contact Information for Business Card

Section for Name
Section for Title

HALVORA - The Strength of Pooling
Mobile:
Direct:

Font styles to use
Sans Serif

Colors
33a6d7
0692cd
0255a3
ffffff

Requirements
Must have
• Logo, all business card details

```html
<!DOCTYPE html>
<html lang="en">
<head>
<meta charset="utf-8">
<title>Halvora Business Card</title>
<link href="https://fonts.googleapis.com/css2?family=Hind:wght@400;500;700&display=swap" rel="stylesheet">
<style>
  :root {
    --bg: #dcdfe3;
    --card: #eef0f2;
    --navy: #1a2a5a;
    --blue: #0692cd;
    --blue-light: #33a6d7;
    --blue-deep: #0255a3;
    --ink: #2d3440;
    --white: #ffffff;
  }
  * { margin: 0; padding: 0; box-sizing: border-box; }
  html, body {
    width: 1200px; height: 970px; overflow: hidden;
    background: var(--bg);
    font-family: "Hind", Arial, sans-serif;
  }
  .business-card {
    position: absolute; left: 160px; top: 235px;
    width: 880px; height: 500px;
    background: var(--card);
    border-radius: 22px; overflow: hidden;
    box-shadow: 0 10px 30px rgba(0,0,0,0.15);
  }
  .card-shapes { position: absolute; inset: 0; width: 100%; height: 100%; }
  .brand {
    position: absolute; left: 56px; top: 62px;
  }
  .brand-name {
    display: block;
    font-weight: 700; font-size: 72px; line-height: 1;
    color: var(--navy); letter-spacing: 1px;
  }
  .brand-tagline {
    display: block; margin-top: 4px;
    font-weight: 500; font-size: 19px; line-height: 1.2;
    color: var(--blue-deep); letter-spacing: 0.5px;
  }
  .person {
    position: absolute; right: 118px; top: 194px; text-align: right;
  }
  .person-name {
    font-weight: 700; font-size: 30px; line-height: 1.1;
    color: var(--navy); letter-spacing: 0.5px;
  }
  .person-title {
    font-weight: 400; font-size: 22px; line-height: 1.2;
    color: var(--blue-deep); margin-top: 4px;
  }
  .address {
    position: absolute; left: 64px; top: 268px;
    font-size: 21px; line-height: 29px; color: var(--ink);
  }
  .contacts {
    position: absolute; left: 64px; top: 340px; list-style: none;
    font-size: 20px; color: var(--ink);
  }
  .contacts li { display: flex; align-items: center; gap: 12px; height: 29px; }
  .contacts svg { width: 16px; height: 16px; fill: var(--ink); flex: none; }
</style>
</head>
<body>
  <div class="business-card">
    <svg class="card-shapes" viewBox="0 0 880 500" preserveAspectRatio="none">
      <path d="M722,0 C860,80 880,330 490,500 L880,500 L880,0 Z" fill="var(--navy)"/>
      <path d="M838,190 C850,330 730,455 560,500 L490,500 C760,410 852,310 838,190 Z" fill="var(--blue)"/>
      <path d="M826,220 C830,330 720,440 530,500" fill="none" stroke="var(--blue-light)" stroke-width="3" opacity="0.7"/>
    </svg>

    <div class="brand">
      <span class="brand-name">HALVORA</span>
      <span class="brand-tagline">The Strength of Pooling</span>
    </div>

    <div class="person">
      <div class="person-name">DANIEL REEVE</div>
      <div class="person-title">CEO/FOUNDER</div>
    </div>

    <div class="address">
      412 Larkfield Road<br>
      Sydney, NSW 2000
    </div>

    <ul class="contacts">
      <li>
        <svg viewBox="0 0 16 16"><path d="M3.5 1 L6 1 L7 4.5 L5.5 6 C6.5 8 8 9.5 10 10.5 L11.5 9 L15 10 L15 12.5 C15 13.9 13.9 15 12.5 15 C6.5 15 1 9.5 1 3.5 C1 2.1 2.1 1 3.5 1 Z"/></svg>
        <span>02 8123 4567</span>
      </li>
      <li>
        <svg viewBox="0 0 16 16"><path d="M4 0 H12 A1.5 1.5 0 0 1 13.5 1.5 V14.5 A1.5 1.5 0 0 1 12 16 H4 A1.5 1.5 0 0 1 2.5 14.5 V1.5 A1.5 1.5 0 0 1 4 0 Z M4.5 2 V12.5 H11.5 V2 Z M7 13.5 V15 H9 V13.5 Z"/></svg>
        <span>0412 555 019</span>
      </li>
      <li>
        <svg viewBox="0 0 16 16"><path d="M1 3 H15 V4 L8 9 L1 4 Z M1 5.5 L8 10.5 L15 5.5 V13 H1 Z"/></svg>
        <span>daniel@halvora.com</span>
      </li>
      <li>
        <svg viewBox="0 0 16 16"><circle cx="8" cy="8" r="7"/><path d="M1 8 H15 M8 1 C5 4 5 12 8 15 M8 1 C11 4 11 12 8 15" stroke="var(--card)" stroke-width="1.2" fill="none"/></svg>
        <span>www.halvora.com</span>
      </li>
    </ul>
  </div>
</body>
</html>
```